Typography of the cover "Watch the tide turning"

We would like to improve the presentation of a book cover: presentation and typography of the authors and of the title. Image of the cover is available in two versions (with or without sky), joined with the texts (joined files): Mathis Corvenot Watched the turning tide Romance Editions Murlane

Industry/Entity Type

Publishing

Colors

Designer to choose colors to be used in the design.

Requirements
Must have
• Provided picture (with or without sky)

```html
<!DOCTYPE html>
<html lang="en">
<head>
<meta charset="utf-8">
<title>Watch the tide turning — Mathis Corvenot</title>
<link rel="stylesheet" href="https://fonts.googleapis.com/css2?family=Anton&family=Montserrat:wght@800&display=swap">
<style>
  :root {
    --sky-top: #e4e4e4;
    --sky-mid: #c9c9c9;
    --city-mid: #6e6e6e;
    --city-dark: #1c1c1c;
    --frame: #6a1a16;
    --author-ink: #1e1e1e;
    --title-dark: #5a1612;
    --title-red: #e3222a;
    --title-edge: #ffffff;
    --label-ink: #ffffff;
  }
  html, body {
    margin: 0;
    padding: 0;
    overflow: hidden;
    background: #ffffff;
  }
  .cover {
    position: relative;
    width: 810px;
    height: 1200px;
    overflow: hidden;
  }
  .cover-photo {
    position: absolute;
    inset: 0;
    background: linear-gradient(to bottom,
      var(--sky-top) 0%,
      var(--sky-mid) 45%,
      #a9a9a9 58%,
      var(--city-mid) 72%,
      #3d3d3d 86%,
      var(--city-dark) 100%);
  }
  .cover-type {
    position: absolute;
    inset: 0;
  }
  .author {
    font-family: 'Montserrat', sans-serif;
    font-weight: 800;
    fill: var(--author-ink);
  }
  .title-line {
    font-family: 'Anton', sans-serif;
    fill: url(#titleFill);
    stroke: var(--title-edge);
    stroke-width: 5;
    stroke-linejoin: round;
    paint-order: stroke fill;
  }
  .genre, .publisher {
    font-family: 'Montserrat', sans-serif;
    font-weight: 800;
    fill: var(--label-ink);
  }
  .frame-line {
    stroke: var(--frame);
    stroke-width: 2;
    fill: none;
  }
</style>
</head>
<body>
<div class="cover">
  <div class="cover-photo" role="img" aria-label="Black and white photograph of a dense city skyline under a pale misty sky, blurred vertically"></div>

  <svg class="cover-type" width="810" height="1200" viewBox="0 0 810 1200" xmlns="http://www.w3.org/2000/svg">
    <defs>
      <linearGradient id="titleFill" x1="0" y1="214" x2="0" y2="660" gradientUnits="userSpaceOnUse">
        <stop offset="0" stop-color="var(--title-dark)"/>
        <stop offset="0.55" stop-color="#9a2320"/>
        <stop offset="1" stop-color="var(--title-red)"/>
      </linearGradient>
    </defs>

    <path class="frame-line" d="M214 184 H102 V704 H320"/>
    <path class="frame-line" d="M618 184 H725 V704 H514"/>

    <text class="author" x="416" y="194" text-anchor="middle" font-size="32" textLength="380" lengthAdjust="spacingAndGlyphs">MATHIS CORVENOT</text>

    <text class="title-line" x="128" y="352" font-size="158" textLength="572" lengthAdjust="spacingAndGlyphs">WATCH</text>
    <text class="title-line" x="182" y="506" font-size="158" textLength="466" lengthAdjust="spacingAndGlyphs">THE TIDE</text>
    <text class="title-line" x="154" y="658" font-size="158" textLength="522" lengthAdjust="spacingAndGlyphs">TURNING</text>

    <text class="genre" x="417" y="714" text-anchor="middle" font-size="30" textLength="172" lengthAdjust="spacingAndGlyphs">ROMAN</text>

    <text class="publisher" x="417" y="1078" text-anchor="middle" font-size="20" textLength="258" lengthAdjust="spacingAndGlyphs">EDITIONS MURLANE</text>
  </svg>
</div>
</body>
</html>
```